TWPC Business Card Design

Business card for sole operator professional civil and traffic engineer.
Clients are developers and planners who require assistance with traffic strategic master planning advice and design development for access and infrastructure associated with the development.
Colours already in use are greens for the business name and black for other legend. The attached file shows the letterhead template which is currently in use.
Target Market(s)
Professional Clients in development industry
Most clients known to the Principal and card is mostly required to allow ongoing contact
Industry/Entity Type
Business
Contact Information for Business Card
LACHLAN PETTIGREW CONSULTING PARTNERS
ABN 37 814 529 106
PO Box 418 KELWOOD NSW 2619
Lachlan Pettigrew 0412 358 971
l.pettigrew@corvanmail.net

```html
<!DOCTYPE html>
<html lang="en">
<head>
<meta charset="utf-8">
<title>TWPC Business Card</title>
<link href="https://fonts.googleapis.com/css2?family=Cinzel:wght@400&family=Roboto:wght@400;900&display=swap" rel="stylesheet">
<style>
  :root {
    --backdrop: #e6e6e4;
    --card: #ffffff;
    --brand-green: #8cc425;
    --ink: #111111;
    --on-green: #ffffff;
  }
  * { margin: 0; padding: 0; box-sizing: border-box; }
  html, body { width: 1200px; height: 960px; overflow: hidden; }
  body {
    background: var(--backdrop);
    font-family: "Roboto", Arial, sans-serif;
    position: relative;
  }
  .business-card {
    position: absolute;
    left: 100px;
    top: 180px;
    width: 1000px;
    height: 600px;
    background: var(--card);
    box-shadow: 0 10px 30px rgba(0,0,0,0.18);
    overflow: hidden;
  }
  .company-block {
    position: absolute;
    right: 60px;
    top: 66px;
    text-align: right;
  }
  .company-name {
    font-weight: 900;
    font-size: 31px;
    letter-spacing: -0.4px;
    color: var(--brand-green);
    line-height: 1.1;
  }
  .company-abn {
    font-size: 21px;
    color: var(--ink);
    margin-top: 2px;
  }
  .contact-list {
    position: absolute;
    right: 58px;
    top: 272px;
    list-style: none;
    text-align: right;
  }
  .contact-item {
    display: flex;
    justify-content: flex-end;
    align-items: center;
    gap: 14px;
    font-size: 21px;
    color: var(--ink);
    line-height: 30px;
  }
  .contact-icon { width: 16px; height: 16px; fill: var(--ink); flex: none; }
  .name-band {
    position: absolute;
    left: 0;
    bottom: 0;
    width: 100%;
    height: 120px;
    background: var(--brand-green);
  }
  .person-name {
    position: absolute;
    right: 270px;
    top: 38px;
    font-family: "Cinzel", Georgia, serif;
    font-size: 36px;
    color: var(--on-green);
    letter-spacing: 1px;
  }
</style>
</head>
<body>
  <section class="business-card">
    <header class="company-block">
      <h1 class="company-name">LACHLAN PETTIGREW CONSULTING PARTNERS</h1>
      <p class="company-abn">ABN 37 814 529 106</p>
    </header>

    <ul class="contact-list">
      <li class="contact-item">
        <span>0412 358 971</span>
        <svg class="contact-icon" viewBox="0 0 16 16" aria-hidden="true"><path d="M1 5c0-2 2-3 7-3s7 1 7 3v1h-4V4.5H5V6H1z"/><path d="M3 8l2-2h6l2 2v6H3z"/><circle cx="8" cy="10.5" r="1.6" fill="#fff"/></svg>
      </li>
      <li class="contact-item">
        <span>PO Box 418 KELWOOD NSW 2619</span>
        <svg class="contact-icon" viewBox="0 0 16 16" aria-hidden="true"><path d="M8 1a5 5 0 0 0-5 5c0 4 5 9 5 9s5-5 5-9a5 5 0 0 0-5-5z"/><circle cx="8" cy="6" r="1.8" fill="#fff"/></svg>
      </li>
      <li class="contact-item">
        <span>l.pettigrew@corvanmail.net</span>
        <svg class="contact-icon" viewBox="0 0 16 16" aria-hidden="true"><rect x="1" y="3" width="14" height="10"/><path d="M1.5 3.5L8 9l6.5-5.5" fill="none" stroke="#fff" stroke-width="1.4"/></svg>
      </li>
    </ul>

    <footer class="name-band">
      <p class="person-name">Lachlan Pettigrew</p>
    </footer>
  </section>
</body>
</html>
```